Visitenkarten-Design für Anbieter von Softwarelösungen rund ums Bargeld
Unser Favorit war gleich beim 1. Entwurf mit dabei. Schön war vor allem, dass uns gleich 3 verschiedene Farbvarianten angeboten wurden. Daher bedurfte es auch keinerlei Anpassungen von unserer Seite. Herzlichen Dank!
Zielgruppe
Unsere Unternehmensgruppe, bestehend aus mehreren Tochterunternehmen, ist ein führender europäischer Anbieter für Softwarelösungen rund ums Bargeld.
Unsere Lösungen unterstützen Handelsunternehmen, Wertdienstleister und Finanzinstitute bei der Erfassung und Nachverfolgung von Zahlungsströmen im Bargeldkreislauf (Cash Management + Track & Trace). Bargeldmanagementprozesse werden durch unsere Produkte bei unseren Kunden optimiert, Verwaltungs-, Prozess- und Personalkosten gesenkt: Für mehr Sicherheit, Effizienz und Transparenz.
Es ist wahrscheinlich, dass wir zukünftig mittels Zukäufen über unsere derzeitigen Tätigkeitsfelder hinaus wachsen. Neben Cash wird die (Werte-)Logistik bzw. Logistik generell eine Rolle spielen. Auch unter der Maßgabe, dass zukünftig nur noch Services (statt Verkauf von Software) angeboten werden.
Der Fokus wird sich weiterhin primär auf Geschäftskunden beschränken: Wir helfen Unternehmen, effizienter zu werden.
www.digital.kestoro-beispiel.eu
Aufgabenstellung
Die Schreibweise unseres Namens sieht wie folgt aus: 'KESTORO | Digital Solutions'
Die Farbcodes des Logo sind in der Datei abgebildet.
Als ergänzende Farben nutzen wir aktuell ein Türkis (CMYK: 53/23/21/0 | #86ACBA) und ein Dunkelgrau (CMYK: 77/62/38/21 | #44546A). Diese dürfen gerne mit verwendet werden.

```html
<!DOCTYPE html>
<html lang="de">
<head>
<meta charset="utf-8">
<title>KESTORO | Digital Solutions – Visitenkarten</title>
<link rel="stylesheet" href="https://fonts.googleapis.com/css2?family=Montserrat:wght@600;700&family=Michroma&display=swap">
<style>
  :root {
    --maroon: #8b2f42;
    --grey-line: #b3b3b3;
    --text-grey: #6e6e6e;
    --paper: #ffffff;
    --backdrop: #dcdcdc;
  }
  * { margin: 0; padding: 0; box-sizing: border-box; }
  html, body { width: 1200px; height: 842px; overflow: hidden; }
  body {
    background: var(--backdrop);
    position: relative;
    font-family: "Montserrat", sans-serif;
  }
  .card {
    position: absolute;
    top: 258px;
    width: 520px;
    height: 325px;
    box-shadow: 0 6px 18px rgba(0,0,0,0.15);
    overflow: hidden;
  }
  .card--front { left: 50px; background: var(--maroon); color: var(--paper); }
  .card--back { left: 630px; background: var(--paper); }

  .brand { display: flex; align-items: center; }
  .brand-dot { border-radius: 50%; flex: none; }
  .brand-rule { width: 1px; flex: none; }
  .brand-name { font-weight: 700; line-height: 1; letter-spacing: 1px; white-space: nowrap; }
  .brand-name small { display: block; font-size: 0.33em; letter-spacing: 2px; margin-top: 4px; }

  /* front */
  .front-brand { position: absolute; left: 62px; top: 82px; gap: 20px; }
  .front-brand .brand-dot { width: 62px; height: 62px; border: 4px solid var(--paper); }
  .front-brand .brand-rule { height: 84px; background: var(--paper); }
  .front-brand .brand-name { font-size: 52px; }
  .front-tagline {
    position: absolute; left: 0; right: 0; top: 212px;
    text-align: center; font-weight: 700; font-size: 20px; letter-spacing: 1.5px;
  }

  /* back */
  .back-brand { position: absolute; left: 28px; top: 108px; gap: 12px; color: var(--maroon); }
  .back-brand .brand-dot { width: 38px; height: 38px; border: 3px solid var(--maroon); }
  .back-brand .brand-rule { height: 56px; background: var(--grey-line); }
  .back-brand .brand-name { font-size: 30px; }
  .back-divider {
    position: absolute; left: 282px; top: 58px; width: 1px; height: 170px;
    background: var(--grey-line);
  }
  .contact {
    position: absolute; left: 298px; top: 56px;
    font-family: "Michroma", sans-serif; font-size: 10px; line-height: 1.5;
    color: var(--text-grey);
  }
  .contact__name { color: var(--maroon); font-size: 14px; line-height: 1.2; }
  .contact__role { margin-bottom: 14px; }
  .contact__address { margin-bottom: 8px; }
  .stripes { position: absolute; left: 0; right: 0; top: 240px; }
  .stripe { height: 5px; background: var(--grey-line); }
  .stripe-row {
    display: flex; align-items: center; gap: 10px; height: 22px;
  }
  .stripe--accent { height: 7px; background: var(--maroon); flex: 1; }
  .stripe--accent-short { flex: none; width: 24px; }
  .website {
    font-family: "Michroma", sans-serif; font-size: 10.5px; color: var(--text-grey);
    white-space: nowrap;
  }
  .stripes .stripe + .stripe-row { margin-top: 4px; }
  .stripe-row + .stripe { margin-top: 4px; }
</style>
</head>
<body>
  <section class="card card--front">
    <div class="brand front-brand">
      <span class="brand-dot"></span>
      <span class="brand-rule"></span>
      <div class="brand-name">KESTORO<small>DIGITAL SOLUTIONS</small></div>
    </div>
    <p class="front-tagline">BARGELD SERVICE HOLDING AG</p>
  </section>

  <section class="card card--back">
    <div class="brand back-brand">
      <span class="brand-dot"></span>
      <span class="brand-rule"></span>
      <div class="brand-name">KESTORO<small>DIGITAL SOLUTIONS</small></div>
    </div>
    <div class="back-divider"></div>
    <div class="contact">
      <p class="contact__name">Lukas Brenner</p>
      <p class="contact__role">Managing</p>
      <p class="contact__address">Lindenhof 7<br>04109 Leipzig<br>Germany</p>
      <p>Tel.: +49 341 555010-00<br>Fax: +49 341 555010-89<br>E-Mail: info@kestoro-beispiel.de</p>
    </div>
    <div class="stripes">
      <div class="stripe"></div>
      <div class="stripe-row">
        <span class="stripe--accent"></span>
        <span class="website">www.digital.kestoro-beispiel.eu</span>
        <span class="stripe--accent stripe--accent-short"></span>
      </div>
      <div class="stripe"></div>
    </div>
  </section>
</body>
</html>
```